Chimney Service company needs new business card design

We need a updated business card with our new logo added. We provide a full range of chimney services throughout Vermont and New Hampshire. The business card will be one sided and color. Attached is our current business card another document showing all the information we would like on the card.
We dont like a lot of flashy colors.... here is a link to our website to get an idea of our branding www.flueguardianvt.example

Target Market(s)

homeowners

Industry/Entity Type

Business

Contact Information for Business Card

See attached sheet for content.

Font styles to use
Serif
Sans Serif

Requirements
Must have
• all information provided on separate sheet
Should not have
• Additional information that may clogg up design

```html
<!DOCTYPE html>
<html lang="en">
<head>
<meta charset="utf-8">
<title>Flue Guardian Business Card</title>
<link href="https://fonts.googleapis.com/css2?family=Open+Sans:wght@400;600;700&family=Michroma&display=swap" rel="stylesheet">
<style>
  :root {
    --backdrop: #3a3a3a;
    --card: #232323;
    --card-front: #1c1c1c;
    --ink: #ffffff;
    --muted: #d9d9d9;
    --emboss: #3c3c3c;
    --red: #b3131b;
    --red-bright: #d62027;
  }
  * { margin: 0; padding: 0; box-sizing: border-box; }
  html, body { width: 799px; height: 1200px; overflow: hidden; }
  body {
    background: var(--backdrop);
    font-family: "Open Sans", Arial, sans-serif;
    color: var(--ink);
    position: relative;
  }
  .card {
    position: absolute;
    left: 60px;
    width: 680px;
    height: 389px;
    border-radius: 4px;
    overflow: hidden;
    box-shadow: 0 12px 30px rgba(0,0,0,.45);
  }
  .card--front { top: 150px; background: var(--card-front); }
  .card--back { top: 660px; background: var(--card); }

  /* front */
  .front-brand {
    position: absolute; left: 0; right: 0; top: 150px;
    display: flex; align-items: center; justify-content: center; gap: 16px;
  }
  .brand-square { width: 30px; height: 30px; border: 4px solid var(--emboss); }
  .front-brand .brand-name {
    font-size: 38px; font-weight: 600; letter-spacing: 3px; color: var(--emboss);
    text-transform: uppercase;
  }
  .front-est {
    position: absolute; left: 0; right: 0; top: 210px; text-align: center;
    font-size: 16px; letter-spacing: 4px; color: var(--emboss);
  }

  /* back */
  .back-brand {
    position: absolute; left: 30px; top: 150px; width: 300px;
    display: flex; align-items: center; gap: 12px; justify-content: center;
  }
  .back-brand .brand-square { border-color: var(--ink); width: 24px; height: 24px; border-width: 3px; }
  .back-brand .brand-name {
    font-size: 28px; font-weight: 600; letter-spacing: 2px; text-transform: uppercase;
  }
  .back-est {
    position: absolute; left: 30px; width: 300px; top: 196px; text-align: center;
    font-size: 13px; letter-spacing: 3px;
  }
  .back-est::before, .back-est::after {
    content: ""; display: inline-block; width: 70px; height: 1px; background: var(--ink);
    vertical-align: middle; margin: 0 10px;
  }

  .services {
    position: absolute; left: 390px; top: 40px; list-style: none;
    font-size: 15px; line-height: 22px;
  }
  .services li { display: flex; align-items: center; gap: 8px; }
  .services li::before {
    content: ""; width: 7px; height: 7px; border-radius: 50%; background: var(--red-bright);
  }

  .service-area {
    position: absolute; left: 390px; top: 162px;
    font-family: "Michroma", "Arial Black", sans-serif; font-size: 19px; line-height: 24px;
    font-weight: 700; text-transform: uppercase;
  }
  .service-area .rule { display: block; width: 230px; height: 2px; background: var(--red-bright); margin: 6px 0 4px; }
  .service-area .since { display: block; font-family: "Open Sans", Arial, sans-serif; font-size: 11px; line-height: 14px; font-weight: 400; padding-left: 80px; }

  .contact {
    position: absolute; left: 390px; top: 256px; list-style: none;
    font-size: 15px; line-height: 24px;
  }
  .contact li { display: flex; align-items: center; gap: 10px; }
  .contact svg { width: 14px; height: 14px; fill: var(--red-bright); flex: none; }
  .contact .accent { color: var(--red-bright); }

  .promise-band {
    position: absolute; left: 0; right: 0; bottom: 0; height: 46px;
    background: var(--red);
    display: flex; align-items: center; padding-left: 30px; gap: 18px;
    font-size: 14px;
  }
</style>
</head>
<body>
  <section class="card card--front" aria-label="Card front">
    <div class="front-brand">
      <span class="brand-square"></span>
      <span class="brand-name">Flue Guardian</span>
    </div>
    <p class="front-est">INC 1989</p>
  </section>

  <section class="card card--back" aria-label="Card back">
    <div class="back-brand">
      <span class="brand-square"></span>
      <span class="brand-name">Flue Guardian</span>
    </div>
    <p class="back-est">INC 1989</p>

    <ul class="services">
      <li>Full Masonry Services</li>
      <li>Historic chimney restoration</li>
      <li>Stainless steel liners</li>
      <li>New Chimney Installations</li>
      <li>NHCA Certified Chimney sweeps</li>
    </ul>

    <h2 class="service-area">Serving VT and<br>New Hampshire
      <span class="rule"></span>
      <span class="since">SINCE 1989</span>
    </h2>

    <ul class="contact">
      <li><svg viewBox="0 0 16 16" aria-hidden="true"><path d="M3 1h3l1.5 4-2 1.3a9 9 0 0 0 4.2 4.2L11 8.5l4 1.5v3a2 2 0 0 1-2 2A13 13 0 0 1 1 3a2 2 0 0 1 2-2z"/></svg>802-555-0147</li>
      <li><svg viewBox="0 0 16 16" aria-hidden="true"><path d="M1 3h14v10H1z M1.5 3.5 8 9l6.5-5.5" stroke="#232323" stroke-width="1.2"/></svg>info@flueguardianvt.example</li>
      <li><svg viewBox="0 0 16 16" aria-hidden="true"><circle cx="8" cy="8" r="7"/><path d="M1 8h14M8 1c-3 3-3 11 0 14M8 1c3 3 3 11 0 14" stroke="#232323" stroke-width="1" fill="none"/></svg>www.<span class="accent">flueguardianvt</span>.example</li>
    </ul>

    <div class="promise-band">
      <span>Fully Insured – Free Estimates</span>
      <span>|</span>
      <span>Family Owned &amp; Operated</span>
    </div>
  </section>
</body>
</html>
```